Personal Care and Home care ingredients Brochure

We need a flyer or brochure of the of chemicals we distribute for the manufacturing of personal care products such as shampoos, liquid soaps, creams, lotions, conditioners, hand sanitizer, Hair Jellys, etc and for Home care products such as, liquid soaps, desinfectants, cleaners, stain removers,etc.
The idea is to send this pdf brochure via email and companies feel very confortable with the impression it gives. We want to call attention.
Target Market(s)
Companies that manufactures cosmetics, personal care products and home care products.
Font styles to use
Colors
Designer to choose colors to be used in the design.
Requirements
Must have
- Images that refers to the skin, hair, cleaning, washing

```html
<!DOCTYPE html>
<html lang="en">
<head>
<meta charset="utf-8">
<title>Lumera Quimica – Ingredients Brochure Cover</title>
<link rel="stylesheet" href="https://fonts.googleapis.com/css2?family=Montserrat:wght@500;800&display=swap">
<style>
  :root {
    --backdrop: #141414;
    --paper: #ffffff;
    --ink: #111111;
    --descriptor-grey: #9a9a96;
    --hair-dark: #16170f;
    --hair-shadow: #3a3522;
    --hair-olive: #8b9645;
    --hair-warm: #a88a5a;
    --hair-towel: #2e2c38;
    --wash-teal: #1d5556;
    --wash-deep: #173f40;
    --wash-green: #3a9a45;
    --wash-mint: #4c9c88;
    --brand-teal: #3a9c8a;
  }
  * { margin: 0; padding: 0; box-sizing: border-box; }
  html, body {
    width: 1200px; height: 1200px; overflow: hidden;
    background: var(--backdrop);
  }
  .brochure-cover {
    position: absolute;
    left: 207px; top: 71px;
    width: 763px; height: 1078px;
    background: var(--paper);
    overflow: hidden;
  }
  .cover-art { position: absolute; inset: 0; width: 100%; height: 100%; display: block; }
  .brand-card {
    position: absolute;
    left: 237px; top: 389px;
    width: 278px; height: 278px;
    background: var(--paper);
    border-radius: 26px;
    box-shadow: 4px 6px 8px rgba(0,0,0,0.25);
  }
  .brand-mark {
    position: absolute;
    left: 114px; top: 71px;
    width: 56px; height: 56px;
    background: var(--brand-teal);
  }
  .brand-name {
    position: absolute;
    left: 0; right: 0; top: 150px;
    font-family: "Montserrat", sans-serif;
    font-weight: 800;
    font-size: 47px;
    line-height: 1;
    letter-spacing: -0.5px;
    color: var(--ink);
    text-align: center;
  }
  .brand-descriptor {
    position: absolute;
    left: 0; right: 0; top: 204px;
    font-family: "Montserrat", sans-serif;
    font-weight: 500;
    font-size: 24px;
    line-height: 1;
    letter-spacing: 16px;
    padding-left: 16px;
    color: var(--descriptor-grey);
    text-align: center;
  }
</style>
</head>
<body>
  <main class="brochure-cover">
    <svg class="cover-art" viewBox="0 0 1228 1736" preserveAspectRatio="none">
      <defs>
        <linearGradient id="hairTones" x1="0" y1="0" x2="1" y2="0.7">
          <stop offset="0" stop-color="var(--hair-dark)"/>
          <stop offset="0.3" stop-color="var(--hair-shadow)"/>
          <stop offset="0.55" stop-color="var(--hair-warm)"/>
          <stop offset="0.8" stop-color="var(--hair-olive)"/>
          <stop offset="1" stop-color="var(--hair-towel)"/>
        </linearGradient>
        <linearGradient id="washTones" x1="0" y1="0" x2="0.25" y2="1">
          <stop offset="0" stop-color="var(--wash-deep)"/>
          <stop offset="0.35" stop-color="var(--wash-teal)"/>
          <stop offset="0.65" stop-color="var(--wash-mint)"/>
          <stop offset="1" stop-color="var(--wash-green)"/>
        </linearGradient>
      </defs>
      <polygon class="photo-hair" role="img" aria-label="Photo: hands working shampoo through wet hair at a salon wash"
               points="0,0 1228,0 1228,1226" fill="url(#hairTones)"/>
      <polygon class="photo-cleaning" role="img" aria-label="Photo: detergent bottle standing in a wash basin with rubber gloves"
               points="0,506 1228,1736 0,1736" fill="url(#washTones)"/>
    </svg>

    <div class="brand-card">
      <div class="brand-mark"></div>
      <h1 class="brand-name">LUMERA</h1>
      <p class="brand-descriptor">QUIMICA</p>
    </div>
  </main>
</body>
</html>
```